Detail Shop Business card design

i need a business card design for my new detailing company called 'Brisk's Polish Works'. i want an all black and white design . simple, direct and to the point. i want the designer to choose a fitting font to match the logothe front should have logo, address, phone and email and the back side should have a slogan and text indicating that we offer services on anything including cars, trucks, motorcycles and RVs. slogan will read "we take pride in your ride"
maybe also very small on the back side the IG icon with Brisks_Polish_Works

phone 208.417.6352
address 3847 E Larkin Ave
Spokane WA 99214
email: BrisksPolish@mailvexo.com

Target Market(s)

all ages , auto enthusiasts

Industry/Entity Type

Automotive

Contact Information for Business Card

the front should have logo, address, phone and email and the back side should have a slogan and text indicating that we offer services on anything including cars, trucks, motorcycles and RVs. slogan will read "we take pride in your ride"

phone 208.417.6352
address 3847 E Larkin Ave
Spokane WA 99214

Colors
000000
ffffff

Requirements
Must have
• bold font and very simple design with good spacing
Nice to have
• anything creative from the designer indicating we service any types of vehicles
Should not have
• any colors ,

```html
<!DOCTYPE html>
<html lang="en">
<head>
<meta charset="UTF-8">
<title>Brisk's Polish Works — Business Card</title>
<link rel="stylesheet" href="https://fonts.googleapis.com/css2?family=Cinzel:wght@600;700&family=Lato:wght@400;900&display=swap">
<style>
  :root {
    --ink: #000000;
    --paper: #ffffff;
    --stage: #3a3a3a;
    --ghost: #e2e2e2;
    --rule: #111111;
  }
  * { box-sizing: border-box; margin: 0; padding: 0; }
  html, body {
    width: 1200px; height: 782px; overflow: hidden;
    background: var(--stage);
  }
  .stage {
    width: 1200px; height: 782px;
    display: flex; align-items: center; justify-content: center; gap: 40px;
  }
  .card {
    position: relative;
    width: 540px; height: 309px;
    background: var(--paper);
    overflow: hidden;
    box-shadow: 0 6px 18px rgba(0,0,0,.45);
  }

  /* faint vehicle artwork area */
  .vehicle-art {
    position: absolute;
    right: 0; bottom: 0;
    width: 200px; height: 170px;
    background: radial-gradient(ellipse at 80% 85%, var(--ghost) 0%, rgba(226,226,226,.6) 45%, rgba(255,255,255,0) 75%);
  }

  /* contact side */
  .contact .edge-bar {
    position: absolute; left: 44px; width: 22px; background: var(--ink);
  }
  .contact .edge-bar.top { top: 0; height: 52px; }
  .contact .edge-bar.bottom { bottom: 0; height: 60px; }
  .contact-list {
    position: absolute; left: 46px; top: 80px;
    list-style: none;
    font-family: 'Lato', sans-serif; font-size: 15px; color: var(--ink);
  }
  .contact-list li { display: flex; align-items: flex-start; gap: 9px; margin-bottom: 7px; line-height: 1.15; }
  .contact-list svg { flex: none; width: 18px; height: 18px; }
  .brand-mark {
    position: absolute; right: 60px; bottom: 58px;
    display: flex; align-items: center; gap: 10px;
    font-family: 'Lato', sans-serif; font-weight: 900; font-size: 22px;
    color: var(--ink); letter-spacing: .5px;
  }
  .brand-mark .dot { width: 16px; height: 16px; border-radius: 50%; background: var(--ink); }

  /* slogan side */
  .slogan-side .slogan {
    position: absolute; left: 0; right: 0; top: 78px;
    text-align: center;
    font-family: 'Cinzel', serif; font-weight: 700; font-size: 27px; line-height: 1.15;
    color: var(--ink); letter-spacing: 1px;
  }
  .slogan-side .rule {
    position: absolute; left: 140px; width: 260px; top: 158px;
    height: 2px; background: var(--rule);
  }
  .slogan-side .services {
    position: absolute; left: 0; right: 0; top: 180px;
    text-align: center;
    font-family: 'Lato', sans-serif; font-size: 14px; line-height: 1.3; color: var(--ink);
  }
</style>
</head>
<body>
<main class="stage">

  <section class="card slogan-side">
    <div class="vehicle-art" role="img" aria-label="Faint grey illustration of a classic car wheel and fender"></div>
    <h1 class="slogan">WE TAKE PRIDE<br>IN YOUR RIDE</h1>
    <div class="rule"></div>
    <p class="services">We offer services on anything including<br>cars, trucks, motorcycles and RVs.</p>
  </section>

  <section class="card contact">
    <div class="vehicle-art" role="img" aria-label="Faint grey illustration of a classic car wheel and fender"></div>
    <div class="edge-bar top"></div>
    <div class="edge-bar bottom"></div>
    <ul class="contact-list">
      <li>
        <svg viewBox="0 0 20 20" aria-hidden="true"><circle cx="10" cy="10" r="9" fill="none" stroke="#000" stroke-width="1.6"/><path d="M7 5.5c-1.5 1-1.2 3.5.8 5.8s4.3 3 5.6 2l.6-1-1.8-1.5-1 .8c-.8-.3-2-1.5-2.4-2.4l.8-1L8 5z" fill="#000"/></svg>
        <span>208.417.6352</span>
      </li>
      <li>
        <svg viewBox="0 0 20 20" aria-hidden="true"><circle cx="10" cy="10" r="9" fill="#000"/><rect x="5" y="6.5" width="10" height="7" fill="none" stroke="#fff" stroke-width="1.2"/><path d="M5 6.5l5 4 5-4" fill="none" stroke="#fff" stroke-width="1.2"/></svg>
        <span>BrisksPolish@mailvexo.com</span>
      </li>
      <li>
        <svg viewBox="0 0 20 20" aria-hidden="true"><circle cx="10" cy="10" r="9" fill="none" stroke="#000" stroke-width="1.6"/><path d="M10 4.5a3.5 3.5 0 0 0-3.5 3.5c0 2.6 3.5 7 3.5 7s3.5-4.4 3.5-7A3.5 3.5 0 0 0 10 4.5z" fill="#000"/><circle cx="10" cy="8" r="1.3" fill="#fff"/></svg>
        <span>3847 E Larkin Ave<br>Spokane WA 99214</span>
      </li>
      <li>
        <svg viewBox="0 0 20 20" aria-hidden="true"><circle cx="10" cy="10" r="8" fill="#000"/></svg>
        <span>Brisks_Polish_Works</span>
      </li>
    </ul>
    <div class="brand-mark"><span class="dot"></span><span>Brisk's Polish Works</span></div>
  </section>

</main>
</body>
</html>
```